Redesign of business card for Cedar Ridge Mechanical

We are looking for a new design for our business cards for Cedar Ridge Mechanical. We are a plumbing & HVAC construction company, operating on the West Coast of Canada and USA. Logo attached.
Industry/Entity Type
Construction - Plumbing & HVAC
Contact Information for Business Card
Name, address, phone numbers, email, website address
Look and feel
Each slider illustrates characteristics of the customer's brand and the style your logo design should communicate.

```html
<!DOCTYPE html>
<html lang="en">
<head>
<meta charset="UTF-8">
<title>Cedar Ridge Mechanical – Business Card</title>
<link href="https://fonts.googleapis.com/css2?family=Poppins:wght@300;400;600&display=swap" rel="stylesheet">
<style>
  :root {
    --backdrop: #222223;
    --card: #1b1b1e;
    --card-edge: #2c2c30;
    --ink: #ffffff;
    --ink-soft: #d9d9dc;
  }
  * { margin: 0; padding: 0; box-sizing: border-box; }
  html, body {
    width: 1200px; height: 780px; overflow: hidden;
    background: var(--backdrop);
    font-family: "Poppins", sans-serif;
    color: var(--ink);
  }
  .canvas {
    position: relative; width: 1200px; height: 780px;
  }
  .card {
    position: absolute; top: 235px;
    width: 540px; height: 310px;
    background: var(--card);
    border: 1px solid var(--card-edge);
    border-radius: 3px;
    box-shadow: 0 18px 40px rgba(0,0,0,.45);
  }
  .card--front { left: 40px; }
  .card--back { left: 620px; display: flex; align-items: center; justify-content: center; }

  .brand { display: flex; align-items: center; gap: 10px; }
  .brand__square { width: 16px; height: 16px; border: 3px solid var(--ink); }
  .brand__name {
    font-weight: 600; text-transform: uppercase; letter-spacing: .04em;
    color: var(--ink); line-height: 1.15;
  }
  .card--front .brand { position: absolute; left: 34px; top: 48px; }
  .card--front .brand__name { font-size: 17px; }
  .card--back .brand { gap: 16px; }
  .card--back .brand__square { width: 30px; height: 30px; border-width: 5px; }
  .card--back .brand__name { font-size: 30px; }

  .address {
    position: absolute; left: 34px; bottom: 34px; width: 210px;
    font-size: 12px; font-weight: 300; color: var(--ink-soft); line-height: 1.5;
  }
  .divider {
    position: absolute; left: 270px; top: 46px; width: 1px; height: 218px;
    background: linear-gradient(to bottom, rgba(255,255,255,0), rgba(255,255,255,.75) 30%, rgba(255,255,255,.75) 70%, rgba(255,255,255,0));
  }
  .person { position: absolute; left: 300px; top: 62px; }
  .person__name { font-size: 26px; line-height: 1.1; font-weight: 300; }
  .person__name strong { font-weight: 600; }
  .person__role { font-size: 13px; font-weight: 300; color: var(--ink-soft); margin-top: 2px; }

  .contacts { position: absolute; left: 300px; top: 160px; list-style: none; }
  .contacts li {
    display: flex; align-items: center; gap: 10px;
    font-size: 13px; font-weight: 300; line-height: 1; margin-bottom: 12px;
  }
  .contacts svg { width: 13px; height: 13px; flex: none; }
</style>
</head>
<body>
<main class="canvas">
  <section class="card card--front">
    <div class="brand">
      <span class="brand__square"></span>
      <span class="brand__name">Cedar Ridge<br>Mechanical</span>
    </div>
    <p class="address">410 Harbor Ln. Suite 12<br>Vancouver, BC V6B 1A1</p>
    <span class="divider"></span>
    <div class="person">
      <h1 class="person__name"><strong>Marta</strong> Kovar</h1>
      <p class="person__role">Founder &amp; CEO</p>
    </div>
    <ul class="contacts">
      <li>
        <svg viewBox="0 0 24 24" fill="#fff"><path d="M6.6 10.8a15.1 15.1 0 0 0 6.6 6.6l2.2-2.2a1 1 0 0 1 1-.25 11.4 11.4 0 0 0 3.6.57 1 1 0 0 1 1 1V20a1 1 0 0 1-1 1A17 17 0 0 1 3 4a1 1 0 0 1 1-1h3.5a1 1 0 0 1 1 1c0 1.25.2 2.45.57 3.57a1 1 0 0 1-.25 1z"/></svg>
        (604) 555-0148
      </li>
      <li>
        <svg viewBox="0 0 24 24" fill="none" stroke="#fff" stroke-width="2"><rect x="3" y="5" width="18" height="14" rx="1"/><path d="M3 6l9 7 9-7"/></svg>
        info@cedarridgemech.com
      </li>
      <li>
        <svg viewBox="0 0 24 24" fill="none" stroke="#fff" stroke-width="2"><circle cx="12" cy="12" r="9"/><path d="M3 12h18M12 3c3 3.2 3 14.8 0 18M12 3c-3 3.2-3 14.8 0 18"/></svg>
        www.cedarridgemech.com
      </li>
    </ul>
  </section>

  <section class="card card--back">
    <div class="brand">
      <span class="brand__square"></span>
      <span class="brand__name">Cedar Ridge<br>Mechanical</span>
    </div>
  </section>
</main>
</body>
</html>
```